Im want a website LIKE VRX's and FleetHollow.com's with product payment options like Trenzo's

I need a website LIKE VRX with a header made EXACTLY LIKE THAT OF FLEETHOLLOWS .

The front page photo should be like that of FLEETHOLLOW's webpage as well.

The name of the website will be called "M.K. (Caldera Key)".

We will be targeting ALL MARKETS in a small town in central Panama and charging businesses "listing fees" like a phone book does but also providing informational blogs, news, and other interesting activities.

THIS IS A MULTI PAGE WEBSITE

THIS IS WHERE VRX's website meets Brivelle/FleetHollow.

Once the layout is built I will tweak and modify, add information, and upload items for sale.

Here is a list of specific categories that should be listed out above the front page header image/search bar

-- Home -- News -- Travel -- Activities -- Shop & Dine -- Store -- More... --

These categories should be spread across the bottom of the page in three sections:

WHATS SO GREAT ABOUT (Caldera Key),
HAND PICKED TOURS
ACTIVITIES etc.

Also lets use www.Trenzo.example 's
"HOT DESTINATIONS"
"BEAT THE BEST PRICES IN BOQUETE"
"OCTOBERS INSIDER PICKS"
"TOP DESTINATIONS"
and spread them in four sections side-by-side near the bottom of the page.

Overall I would like to see the finished product to be something LIKE VRX's and FleetHollows.

WE NEED ONLINE PAYMENT OPTIONS LIKE BRIVELLE'S WEBSITE HAS

This will be a desktop website but should be very mobile friendly as well.

-rodmund

P.S. Good luck!

If it isn't already too late to change the website name, the name of the website should be "Caldera Key". Added Friday, October 9, 2015

What do you guys think the budget should be to win this? Added Saturday, October 10, 2015

www.palmorra.example is the most amazing simple site. Whoever can make me a replica with my specifications will win immediately!!!! Added Sunday, October 18, 2015

OMG www.palmorra.example is the bomb!So simple and elegant. Whoever can make me an EXACT REPLICA OF WWW.PALMORRA.EXAMPLE as my site with the specifications mentioned in my brief will take home the $825.00 immediately! Good luck amigos! Added Sunday, October 18, 2015

Does anybody know how to add recurring monthly billing options on this website? Added Sunday, October 18, 2015

ALL MARKETS

Product

Coded - Design and coding required

5+ page

• Coinvey payment options.
• I must be able to add and remove photos/text and video from the HTML files in the page.
• Be creative my friends, and may the odds be forever in your favor!
• I added some photos of a good layout for our page below.

```html
<!DOCTYPE html>
<html lang="en">
<head>
<meta charset="utf-8">
<title>Caldera Key – Travel</title>
<link href="https://fonts.googleapis.com/css2?family=Roboto:wght@300;400;500;700&family=Open+Sans:wght@400;600&display=swap" rel="stylesheet">
<style>
:root{
  --teal:#18a7b5;
  --teal-dark:#12838e;
  --ink:#2c3136;
  --text:#666b70;
  --muted:#9aa0a5;
  --line:#e3e6e8;
  --gray-bg:#f1f2f3;
  --topbar:#1d2124;
  --footer:#2a2e32;
  --footer-deep:#212427;
  --red:#e5473a;
  --blue:#2f8fd8;
  --white:#fff;
}
*{box-sizing:border-box;margin:0;padding:0}
html,body{width:1200px;height:2796px;overflow:hidden}
body{font-family:"Open Sans",Arial,sans-serif;color:var(--text);background:var(--white);font-size:12px;line-height:1.5}
h1,h2,h3,h4,.nav,.btn{font-family:"Roboto",Arial,sans-serif}
.wrap{width:880px;margin:0 auto;position:relative}

/* top bar */
.topbar{height:28px;background:var(--topbar);color:#b8bdc1;font-size:10px}
.topbar .wrap{display:flex;justify-content:space-between;align-items:center;height:28px}
.social{display:flex;gap:6px}
.social span{width:14px;height:14px;border-radius:50%;background:#4a5156;display:block}
.contact{display:flex;gap:18px}

/* hero */
.hero{height:492px;position:relative;background:linear-gradient(100deg,#2f3b1c 0%,#5b6b2a 25%,#8b8a45 45%,#c9b36a 55%,#6f7a35 70%,#2f3d1e 100%)}
.hero-photo{position:absolute;inset:0}
.header{position:absolute;top:0;left:0;right:0;height:68px;background:rgba(20,24,22,.55)}
.header .wrap{display:flex;justify-content:space-between;align-items:center;height:68px}
.logo{display:flex;align-items:center;gap:8px;font-family:"Roboto",sans-serif;font-size:22px;font-weight:500;color:var(--white)}
.logo i{width:12px;height:12px;background:var(--teal);display:block}
.nav{display:flex;height:68px}
.nav a{color:var(--white);font-size:11px;font-weight:500;text-decoration:none;padding:0 12px;display:flex;align-items:center;letter-spacing:.4px}
.nav a.active{background:var(--teal)}
.hero-copy{position:absolute;left:180px;top:130px}
.hero-title{display:inline-block;background:rgba(255,255,255,.85);color:var(--ink);font-size:30px;font-weight:500;padding:10px 18px;margin-bottom:14px}
.hero-list{list-style:none}
.hero-list li{background:rgba(20,24,22,.72);color:var(--white);font-size:13px;padding:6px 14px 6px 30px;margin-bottom:8px;width:fit-content;position:relative}
.hero-list li:before{content:"";position:absolute;left:12px;top:12px;width:8px;height:8px;border:2px solid var(--white);border-radius:50%}
.hiker{position:absolute;right:180px;top:90px;width:200px;height:402px;background:linear-gradient(180deg,rgba(180,160,120,.35),rgba(60,70,40,.4))}

/* band */
.band{height:120px;background:var(--teal);color:var(--white)}
.band .wrap{display:flex;justify-content:space-between;align-items:center;height:120px}
.band h2{font-size:26px;font-weight:500;margin-bottom:6px}
.band p{font-size:11px;opacity:.9}
.btn{display:inline-block;background:var(--ink);color:var(--white);font-size:12px;font-weight:500;padding:10px 22px;text-decoration:none}

/* packages */
.packages{height:700px;padding-top:54px}
.section-title{text-align:center;color:var(--ink);font-size:24px;font-weight:500}
.filters{display:flex;justify-content:center;gap:4px;margin:16px 0 20px;font-size:12px}
.filters span{padding:3px 10px;color:var(--text)}
.filters span.on{background:var(--teal);color:var(--white)}
.grid{display:grid;grid-template-columns:repeat(3,280px);gap:20px 20px}
.card{position:relative}
.card .photo{height:192px;position:relative}
.card .caption{position:absolute;left:0;right:0;bottom:0;display:flex;justify-content:space-between;padding:6px 10px;color:var(--white);font-size:13px;font-weight:600;background:linear-gradient(transparent,rgba(0,0,0,.55))}
.card .more{position:absolute;right:10px;top:10px;background:var(--teal);color:var(--white);font-size:10px;padding:3px 8px}
.card .ribbon{position:absolute;right:10px;top:32px;background:var(--red);color:var(--white);font-family:"Roboto",sans-serif;font-size:13px;font-weight:700;padding:2px 8px;line-height:1.2;text-align:center}
.card .meta{display:flex;justify-content:space-between;font-size:10px;color:var(--muted);padding:8px 2px;border-bottom:1px solid var(--line)}

/* three-column rows */
.row-gray{height:308px;background:var(--gray-bg);padding-top:34px}
.row-white{height:500px;padding-top:34px}
.cols{display:grid;grid-template-columns:repeat(3,280px);gap:20px}
.col-title{display:flex;align-items:center;gap:8px;color:var(--ink);font-size:18px;font-weight:500;margin-bottom:14px;font-family:"Roboto",sans-serif}
.col-title svg{flex:none}
.dest{display:grid;grid-template-columns:1fr 1fr;gap:8px}
.dest div{display:flex;align-items:center;gap:6px;font-size:10px;color:var(--ink);text-transform:uppercase}
.dest b{width:60px;height:44px;display:block}
.pick{height:210px;position:relative;background:linear-gradient(160deg,#7d8f5c,#4f6b3e 50%,#8a8c7a)}
.pick span{position:absolute;left:0;right:0;bottom:0;background:rgba(0,0,0,.5);color:var(--white);font-size:11px;padding:6px 10px}
.quote{background:var(--white);border:1px solid var(--line);padding:16px;font-size:11px;height:150px;font-style:italic}
.quote-by{text-align:right;font-size:11px;margin-top:10px;color:var(--ink)}
.video{height:164px;background:linear-gradient(180deg,#8fb6d4,#5f89a8 55%,#c69866)}
.video-title{color:var(--teal);font-size:15px;margin:12px 0 6px;font-family:"Roboto",sans-serif}
.video-text{font-size:11px}
.tips{list-style:none}
.tips li{display:flex;gap:10px;padding:8px 0;border-bottom:1px solid var(--line)}
.tips b{width:64px;height:48px;flex:none}
.tips h4{color:var(--teal);font-size:13px;font-weight:500;line-height:1.3}
.tips small{font-size:10px;color:var(--muted)}
.search-form .field{border:1px solid var(--line);height:30px;margin-bottom:8px;padding:6px 10px;font-size:11px;color:var(--muted);display:flex;justify-content:space-between}
.search-form .submit{background:var(--red);color:var(--white);text-align:center;height:30px;line-height:30px;font-size:12px;font-family:"Roboto",sans-serif}

/* twitter band */
.tweets{height:124px;background:var(--teal);color:var(--white)}
.tweets .wrap{display:flex;align-items:center;gap:24px;height:124px}
.tweets .dot{width:36px;height:36px;border-radius:50%;background:rgba(255,255,255,.9);flex:none}
.tweets p{font-size:12px;flex:1}
.tweets .arrows{display:flex;gap:4px}
.tweets .arrows span{width:24px;height:24px;background:rgba(255,255,255,.25);display:flex;align-items:center;justify-content:center}
.gap{height:28px}

/* footer */
.footer{height:452px;background:var(--footer);color:#a5abb0;padding-top:40px}
.fcols{display:grid;grid-template-columns:280px 280px 280px;gap:20px}
.flogo{font-family:"Roboto",sans-serif;color:var(--white);font-size:22px;font-weight:500;margin-bottom:10px;display:flex;gap:8px;align-items:center}
.flogo i{width:12px;height:12px;background:var(--teal);display:block}
.ftext{font-size:11px}
.badges{display:flex;gap:12px;margin-top:20px}
.badges span{width:56px;height:36px;border:2px solid #6c7378;border-radius:4px;display:block}
.ftitle{color:var(--teal);font-family:"Roboto",sans-serif;font-size:14px;font-weight:500;margin-bottom:12px;text-transform:uppercase}
.deals{list-style:none}
.deals li{display:flex;gap:10px;padding:8px 0;border-bottom:1px solid #3a3f44}
.deals b{width:48px;height:38px;flex:none}
.deals h4{color:var(--white);font-size:12px;font-weight:500}
.deals small{color:var(--muted);font-size:10px}
.offer{height:140px;margin-bottom:14px;color:var(--white);display:flex;flex-direction:column;align-items:center;justify-content:center;position:relative;font-family:"Roboto",sans-serif}
.offer.blue{background:linear-gradient(180deg,#3ea3e6,#2379c0)}
.offer.red{background:linear-gradient(180deg,#ef6a50,#c9352a)}
.offer strong{font-size:26px;font-weight:500}
.offer span{font-size:16px}
.offer .tag{position:absolute;left:16px;top:18px;width:40px;height:40px;border:2px solid rgba(255,255,255,.8);border-radius:50%}
.copyright{height:44px;background:var(--footer-deep);color:#7d848a;font-size:10px;text-align:center;line-height:44px}
</style>
</head>
<body>

<div class="topbar">
  <div class="wrap">
    <div class="social"><span></span><span></span><span></span><span></span><span></span></div>
    <div class="contact"><span>hello@calderakey.example</span><span>+507 555 0199</span></div>
  </div>
</div>

<section class="hero">
  <div class="hero-photo" role="img" aria-label="Sunlit forest trail with a backpacker"></div>
  <div class="hiker" role="img" aria-label="Smiling hiker with a large backpack"></div>
  <header class="header">
    <div class="wrap">
      <div class="logo"><i></i>Caldera Key</div>
      <nav class="nav">
        <a class="active">HOME</a><a>PAGES</a><a>PACKAGE</a><a>LOCATIONS</a><a>BLOG</a><a>SHORTCODES</a><a>CONTACT</a>
      </nav>
    </div>
  </header>
  <div class="hero-copy">
    <h1 class="hero-title">Best For Travelling Website</h1>
    <ul class="hero-list">
      <li>Package Post Type</li>
      <li>Booking Form by Formwell</li>
      <li>Package Discount Feature</li>
      <li>Package Filtering System</li>
    </ul>
  </div>
</section>

<section class="band">
  <div class="wrap">
    <div>
      <h2>Prepare To Be Amazed With Your Trip</h2>
      <p>Plan every detail with local guides, handpicked stays and easy booking for your next escape.</p>
    </div>
    <a class="btn">Buy Now</a>
  </div>
</section>

<section class="packages">
  <div class="wrap">
    <h2 class="section-title">Most Popular Packages</h2>
    <div class="filters"><span class="on">All</span><span>Tours</span><span>Rentals</span><span>Restaurants</span><span>Hotels &amp; Hostels</span><span>Real Estate</span><span>Apartments</span></div>
    <div class="grid">
      <article class="card">
        <div class="photo" role="img" aria-label="Paris riverside at dusk" style="background:linear-gradient(160deg,#6d86a8,#c4a57a 60%,#3c4a5a)"><span class="more">Learn More</span><div class="caption"><span>Paris and Bordeaux</span><span>$1,200</span></div></div>
        <div class="meta"><span>15 AUG 2015 – 26 AUG 2015</span><span>6 Days</span></div>
      </article>
      <article class="card">
        <div class="photo" role="img" aria-label="Desert canyon landscape" style="background:linear-gradient(160deg,#7fa4cf,#c7764a 55%,#8a3e26)"><span class="more">Learn More</span><div class="caption"><span>Seattle, LA, Vegas</span><span>$1,500</span></div></div>
        <div class="meta"><span>15 AUG 2015 – 26 AUG 2015</span><span>8 Days</span></div>
      </article>
      <article class="card">
        <div class="photo" role="img" aria-label="Rome skyline with church domes" style="background:linear-gradient(160deg,#9cb8d6,#d8b98a 55%,#9a7a55)"><span class="more">Learn More</span><span class="ribbon">20%<br>Off</span><div class="caption"><span>Rome, Milan, Madrid</span><span>$1,800</span></div></div>
        <div class="meta"><span>15 AUG 2015 – 26 AUG 2015</span><span>9 Days</span></div>
      </article>
      <article class="card">
        <div class="photo" role="img" aria-label="Beach with turquoise water" style="background:linear-gradient(180deg,#76c2e6,#3aa7c4 50%,#e7d7a8)"><span class="more">Learn More</span><div class="caption"><span>Florida Family</span><span>$900</span></div></div>
        <div class="meta"><span>15 AUG 2015 – 26 AUG 2015</span><span>5 Days</span></div>
      </article>
      <article class="card">
        <div class="photo" role="img" aria-label="Ornate fountain in a city square" style="background:linear-gradient(160deg,#a9b9c9,#d7c7a6 55%,#8f7f66)"><span class="more">Learn More</span><span class="ribbon">20%<br>Off</span><div class="caption"><span>Rome City Tour</span><span>$700</span></div></div>
        <div class="meta"><span>15 AUG 2015 – 26 AUG 2015</span><span>4 Days</span></div>
      </article>
      <article class="card">
        <div class="photo" role="img" aria-label="Tropical beach with people on the sand" style="background:linear-gradient(180deg,#6fc0e8,#4bb0cf 45%,#efe0b6)"><span class="more">Learn More</span><div class="caption"><span>Hawaii Life Style</span><span>$2,100</span></div></div>
        <div class="meta"><span>15 AUG 2015 – 26 AUG 2015</span><span>10 Days</span></div>
      </article>
    </div>
  </div>
</section>

<section class="row-gray">
  <div class="wrap cols">
    <div>
      <h3 class="col-title"><svg width="18" height="18" viewBox="0 0 18 18"><circle cx="9" cy="9" r="8" fill="none" stroke="#18a7b5" stroke-width="2"/><circle cx="9" cy="9" r="3" fill="#18a7b5"/></svg>Hot Destinations</h3>
      <div class="dest">
        <div><b role="img" aria-label="Paris view" style="background:#9aa9b8"></b>Paris</div>
        <div><b role="img" aria-label="Florence view" style="background:#c7a67d"></b>Florence</div>
        <div><b role="img" aria-label="Rome view" style="background:#b79b74"></b>Rome</div>
        <div><b role="img" aria-label="Athens view" style="background:#8fb2cf"></b>Athens</div>
        <div><b role="img" aria-label="Venice view" style="background:#7ea3bd"></b>Venice</div>
        <div><b role="img" aria-label="Vienna view" style="background:#a7a08e"></b>Vienna</div>
        <div><b role="img" aria-label="London view" style="background:#8893a0"></b>London</div>
        <div><b role="img" aria-label="Sydney view" style="background:#6fa8cf"></b>Sydney</div>
      </div>
    </div>
    <div>
      <h3 class="col-title"><svg width="18" height="18" viewBox="0 0 18 18"><rect x="1" y="3" width="16" height="14" fill="none" stroke="#18a7b5" stroke-width="2"/><line x1="1" y1="7" x2="17" y2="7" stroke="#18a7b5" stroke-width="2"/></svg>October Insider's Pick</h3>
      <div class="pick" role="img" aria-label="Mountain ruins above green valleys"><span>Machu Picchu Day Trip from Cusco</span></div>
    </div>
    <div>
      <h3 class="col-title"><svg width="18" height="18" viewBox="0 0 18 18"><path d="M2 3h14v9H8l-4 4v-4H2z" fill="none" stroke="#18a7b5" stroke-width="2"/></svg>What Client Say</h3>
      <div class="quote">"Every detail was arranged perfectly. Our guide knew the hidden spots, the hotels were lovely and the booking was simple from start to finish. We are already planning our next trip."</div>
      <p class="quote-by">Marta Velez<br><small>Editor of Road Notes</small></p>
    </div>
  </div>
</section>

<section class="row-white">
  <div class="wrap cols">
    <div>
      <h3 class="col-title"><svg width="18" height="18" viewBox="0 0 18 18"><rect x="1" y="4" width="11" height="10" fill="#18a7b5"/><path d="M12 8l5-3v8l-5-3z" fill="#18a7b5"/></svg>Featured Video</h3>
      <div class="video" role="img" aria-label="Gondola on a canal in Venice"></div>
      <h4 class="video-title">Let see how beautiful venice is</h4>
      <p class="video-text">Take a slow ride along the canals, past old bridges and quiet squares, and discover why this city stays with every traveller long after the trip ends.</p>
    </div>
    <div>
      <h3 class="col-title"><svg width="18" height="18" viewBox="0 0 18 18"><path d="M3 4h12M3 9h12M3 14h12" stroke="#18a7b5" stroke-width="2"/></svg>Tips Before Travel</h3>
      <ul class="tips">
        <li><b role="img" aria-label="Travel photo" style="background:#8db3cf"></b><div><h4>Aenean lacinia bibendum nulla</h4><small>Oct 12, 2015</small></div></li>
        <li><b role="img" aria-label="Travel photo" style="background:#c9a878"></b><div><h4>Post Different Thumb</h4><small>Oct 10, 2015</small></div></li>
        <li><b role="img" aria-label="Travel photo" style="background:#7f9d74"></b><div><h4>Purus Inceptos Euismod Fringilla Leo</h4><small>Oct 08, 2015</small></div></li>
        <li><b role="img" aria-label="Travel photo" style="background:#a28d9c"></b><div><h4>Fringilla Commodo Aenean</h4><small>Oct 05, 2015</small></div></li>
      </ul>
    </div>
    <div>
      <h3 class="col-title"><svg width="18" height="18" viewBox="0 0 18 18"><circle cx="7" cy="7" r="5" fill="none" stroke="#18a7b5" stroke-width="2"/><line x1="11" y1="11" x2="16" y2="16" stroke="#18a7b5" stroke-width="2"/></svg>Search For Package</h3>
      <div class="search-form">
        <div class="field">Key Words</div>
        <div class="field">Location<span>▾</span></div>
        <div class="field">Trip Type<span>▾</span></div>
        <div class="field">Departure Date</div>
        <div class="field">Arrival Date</div>
        <div class="field">Max Budget (USD)</div>
        <div class="submit">Search</div>
      </div>
    </div>
  </div>
</section>

<section class="tweets">
  <div class="wrap">
    <span class="dot"></span>
    <p>RT @calderakey "Booking on the right day is probably more important than searching hard" – tips for travelling smart this season<br><small>2 hours ago</small></p>
    <div class="arrows"><span><svg width="8" height="10"><path d="M7 1L2 5l5 4" fill="none" stroke="#fff" stroke-width="2"/></svg></span><span><svg width="8" height="10"><path d="M1 1l5 4-5 4" fill="none" stroke="#fff" stroke-width="2"/></svg></span></div>
  </div>
</section>
<div class="gap"></div>

<footer class="footer">
  <div class="wrap fcols">
    <div>
      <div class="flogo"><i></i>Caldera Key</div>
      <p class="ftext">Discover tours, stays and local places to eat and shop. We gather trusted listings, travel news and weekly activities so you can plan everything in one place with ease.</p>
      <div class="badges"><span></span><span></span><span></span></div>
    </div>
    <div>
      <h4 class="ftitle">Last Minute Deals</h4>
      <ul class="deals">
        <li><b role="img" aria-label="Rome photo" style="background:#b79b74"></b><div><h4>Rome, Milan, Madrid</h4><small>From $1,800</small></div></li>
        <li><b role="img" aria-label="Rome tour photo" style="background:#a9b9c9"></b><div><h4>Rome City Tour</h4><small>From $700</small></div></li>
        <li><b role="img" aria-label="San Francisco photo" style="background:#c7764a"></b><div><h4>San Francisco</h4><small>From $1,100</small></div></li>
        <li><b role="img" aria-label="Wildlife photo" style="background:#8a8a5a"></b><div><h4>Wild Life Tour</h4><small>From $950</small></div></li>
      </ul>
    </div>
    <div>
      <div class="offer blue"><span class="tag"></span><strong>20% Off</strong><span>Rome, Milan, Madrid</span></div>
      <div class="offer red"><span class="tag"></span><strong>30% Off</strong><span>San Francisco</span></div>
    </div>
  </div>
</footer>
<div class="copyright">Copyright © 2015 All Right Reserved. Caldera Key</div>

</body>
</html>
```